full stationary design for a modern sleek design company

we are a design company that does modern minimalistic interior design works as well as other design services for high end clients.
we need a full stationary design including and not limited to (double sided business card, letter head, envelopes, documents folder...etc) that reflects the modern style design we do.
sleek modern and minimalistic is the requirements.
Updates

please use the latest attached files as there was a slight modification on the logo Added Wednesday, March 1, 2017

minor update on the logo files in JPG and PSD has been updated kindly follow the new attachments. Added Thursday, March 2, 2017

Target Market(s)

modern minimalist clients

Industry/Entity Type

Design Agency

Requirements
Must have
• the logo
Nice to have
• i like the colors in the colored 3D logo attached
Should not have
• too many colors

```html
<!DOCTYPE html>
<html lang="en">
<head>
<meta charset="utf-8">
<title>Halden Studio – Business Card</title>
<link href="https://fonts.googleapis.com/css2?family=Open+Sans:wght@400;600;700&display=swap" rel="stylesheet">
<style>
  :root {
    --backdrop: #ecebe8;
    --brand-orange: #f7941e;
    --card-white: #ffffff;
    --ink-dark: #3a3a3c;
    --ink-light: #ffffff;
  }
  * { margin: 0; padding: 0; box-sizing: border-box; }
  html, body {
    width: 1200px;
    height: 987px;
    overflow: hidden;
    background: var(--backdrop);
    font-family: "Open Sans", Arial, sans-serif;
  }
  .canvas { position: relative; width: 1200px; height: 987px; }

  .card {
    position: absolute;
    width: 610px;
    height: 351px;
    box-shadow: 0 3px 8px rgba(0, 0, 0, 0.18);
  }
  .card--front {
    left: 292px;
    top: 130px;
    background: var(--brand-orange);
    border-radius: 0 176px 176px 0;
    color: var(--ink-light);
  }
  .card--back {
    left: 299px;
    top: 505px;
    background: var(--card-white);
    border-radius: 176px 0 0 176px;
  }

  .contact { position: absolute; left: 62px; top: 66px; }
  .contact__name {
    font-size: 25px;
    font-weight: 700;
    letter-spacing: 0.3px;
    line-height: 1;
  }
  .contact__role { font-size: 16px; margin-top: 6px; }
  .contact__address { font-size: 16px; line-height: 23px; margin-top: 14px; }
  .contact__list { list-style: none; margin-top: 8px; font-size: 16px; }
  .contact__list li {
    display: flex;
    align-items: center;
    height: 23.5px;
  }
  .contact__list svg {
    width: 15px;
    height: 15px;
    margin-right: 8px;
    fill: var(--ink-light);
    flex-shrink: 0;
  }

  .brand {
    position: absolute;
    left: 0;
    right: 0;
    top: 0;
    bottom: 0;
    display: flex;
    align-items: center;
    justify-content: center;
    gap: 14px;
    padding-left: 40px;
  }
  .brand__square {
    width: 34px;
    height: 34px;
    background: var(--brand-orange);
  }
  .brand__name {
    font-size: 34px;
    font-weight: 600;
    letter-spacing: 3px;
    color: var(--ink-dark);
    text-transform: uppercase;
  }
</style>
</head>
<body>
<main class="canvas">
  <section class="card card--front">
    <div class="contact">
      <h1 class="contact__name">NORA VALE</h1>
      <p class="contact__role">CEO&amp;Founder</p>
      <p class="contact__address">412 Linden Row<br>Juneau, Alaska 34210</p>
      <ul class="contact__list">
        <li>
          <svg viewBox="0 0 24 24" aria-hidden="true"><path d="M6.6 10.8a15.1 15.1 0 0 0 6.6 6.6l2.2-2.2c.3-.3.7-.4 1-.2 1.1.4 2.3.6 3.6.6.6 0 1 .4 1 1V20c0 .6-.4 1-1 1A17 17 0 0 1 3 4c0-.6.4-1 1-1h3.5c.6 0 1 .4 1 1 0 1.3.2 2.5.6 3.6.1.3 0 .7-.2 1z"/></svg>
          (555) 214 7730
        </li>
        <li>
          <svg viewBox="0 0 24 24" aria-hidden="true"><path d="M7 1h10a2 2 0 0 1 2 2v18a2 2 0 0 1-2 2H7a2 2 0 0 1-2-2V3a2 2 0 0 1 2-2zm0 3v14h10V4zm5 15.5a1 1 0 1 0 0 2 1 1 0 0 0 0-2z"/></svg>
          (555) 380 1642
        </li>
        <li>
          <svg viewBox="0 0 24 24" aria-hidden="true"><path d="M2 5h20v14H2zm2 2v.5l8 5 8-5V7zm0 2.8V17h16V9.8l-8 5z"/></svg>
          nora@haldenstudio.com
        </li>
        <li>
          <svg viewBox="0 0 24 24" aria-hidden="true"><path d="M12 2a10 10 0 1 0 0 20 10 10 0 0 0 0-20zm-1 17.9A8 8 0 0 1 4.2 10.2L9 15v1a2 2 0 0 0 2 2zm6.9-2.5A2 2 0 0 0 16 16h-1v-3a1 1 0 0 0-1-1H8v-2h2a1 1 0 0 0 1-1V7h2a2 2 0 0 0 2-2v-.4a8 8 0 0 1 2.9 12.8z"/></svg>
          www.haldenstudio.com
        </li>
      </ul>
    </div>
  </section>

  <section class="card card--back">
    <div class="brand">
      <span class="brand__square" aria-hidden="true"></span>
      <span class="brand__name">Halden Studio</span>
    </div>
  </section>
</main>
</body>
</html>
```